WTF!!! We need a modern professional website for a business litigation law firm.

We need a modern, clean, professional and uncomplicated website for a new business trial and litigation law firm called "Haverlock Trial Firm PLLC". Website must be mobile optimized for iPad and smartphone. The law firm specializes in counseling and representing large corporations, small businesses and entrepreneurs in and out of the courtroom. Lawyers in the firm serve as Florida counsel and trial counsel to organizations facing claims involving product liability, premises liability, professional liability, vehicle and transportation liability, warranty claims, construction defects and delay claims, complex business disputes, commercial litigation and bid disputes in State and Federal Courts. The website is mainly to provide information about the firm, and should include sections describing the firm, identifying the Industries Served and Areas of Practice ," a separate page identifying the "Professionals", a separate page for "Resources & Advisories," and a traveling "Connect With Us" button a site visitor can click on that will launch an email to the Firm's general email account. The website should allow us to easily modify the content on these pages, and let us add/modify links to external information sources. We will not sell anything or take payments through the website. We do need to be able to easily upload and update photographs of attorneys and add new attorneys names/email hyperlinks as the firm grows. We would like to add developments in the law or success stories easily and quickly, such as through a blog page. On the "Connect With Us" page the website should have hyperlinks to email the Firm, and there should be hyperlinks to email each professional on the "Professionals" page. The website should be viewable on mobile devices without distortion. The law firm focuses on trial work and should have some imagery associated with courtrooms, but the overall theme of the site should be modern, clean, and communicate sophistication and strength. The website should be made in Wordpress. We have uploaded logo files for Haverlock Trial Firm.

Target Market(s)

Corporations and companies that are looking for legal representation. Other attorneys/legal industry.

Industry/Entity Type

Legal Industry

Coding

Coded - Design and coding required

Number of Pages Required

1 page

Font styles to use
Sans Serif

Requirements
Must have
• Simple, clean, sophisticated, modern website that includes the logo, watermark of logo, and the elements described above.
Nice to have
• Pictures of city scape, buildings, courtroom, team members.

```html
<!DOCTYPE html>
<html lang="en">
<head>
<meta charset="utf-8">
<title>Haverlock Trial Firm PLLC</title>
<link href="https://fonts.googleapis.com/css2?family=Michroma&family=Roboto:ital,wght@0,400;0,500;0,700;1,400&family=Roboto+Slab:wght@400&display=swap" rel="stylesheet">
<style>
:root{
  --blue:#1565c8;
  --blue-dark:#0f52a8;
  --black:#111111;
  --ink:#222222;
  --muted:#666666;
  --light:#f0f0f0;
  --grey-btn:#e2e2e2;
  --white:#ffffff;
}
*{box-sizing:border-box;margin:0;padding:0}
html,body{width:1200px;height:4699px;overflow:hidden}
body{position:relative;font-family:'Roboto',sans-serif;color:var(--ink);background:var(--white)}
.abs{position:absolute}
.display{font-family:'Michroma',sans-serif;letter-spacing:3px;text-transform:uppercase;font-weight:400}
.rule{width:56px;height:3px;background:var(--blue);margin:10px auto 0;border-radius:2px}
.section-title{position:absolute;left:0;width:1200px;text-align:center;font-size:33px;color:var(--black)}

/* header */
.site-header{top:0;left:0;width:1200px;height:118px;background:var(--white)}
.brand{left:100px;top:18px;width:165px;text-align:center;color:var(--black)}
.brand-mark{width:26px;height:26px;background:var(--black);margin:0 auto 8px}
.brand-name{font-size:24px;font-weight:700;letter-spacing:1px;line-height:1}
.brand-sub{font-size:10px;font-weight:700;letter-spacing:3px;margin-top:4px}
.contact-item{top:22px;display:flex;align-items:center;gap:10px}
.contact-icon{width:32px;height:32px;border-radius:50%;background:var(--blue);display:flex;align-items:center;justify-content:center}
.contact-label{font-size:11px;color:var(--muted)}
.contact-value{font-size:16px;font-weight:500;color:var(--black)}
.main-nav{left:383px;top:77px;width:817px;height:41px;background:var(--black);clip-path:polygon(32px 0,100% 0,100% 100%,0 100%)}
.main-nav ul{list-style:none;display:flex;height:100%;padding-left:52px}
.main-nav li{color:var(--white);font-size:13px;font-weight:500;padding:0 15px;display:flex;align-items:center}
.main-nav li.active{background:var(--blue)}

/* hero */
.hero{top:118px;left:0;width:1200px;height:535px;background:linear-gradient(180deg,#8d98a4 0%,#6c7683 45%,#4b5560 100%)}
.hero-arrow{top:364px;width:42px;height:42px;border-radius:50%;background:rgba(20,20,20,.75);display:flex;align-items:center;justify-content:center}
.hero-banner{left:188px;top:560px;width:824px;height:179px;background:var(--black)}
.hero-banner .slant{position:absolute;left:82px;top:0;width:660px;height:179px;background:var(--blue);clip-path:polygon(18% 0,100% 0,82% 100%,0 100%)}
.hero-banner .bracket{position:absolute;top:18px;width:64px;height:143px;border:3px solid var(--white)}
.hero-banner .bracket.l{left:18px;border-right:none}
.hero-banner .bracket.r{right:18px;border-left:none}
.hero-banner h1{position:absolute;left:0;width:100%;top:42px;text-align:center;color:var(--white);font-size:33px;line-height:44px}

/* practice */
.practice-card{width:305px;height:192px;display:flex;align-items:center;justify-content:center;text-align:center;color:var(--white);font-size:20px;font-weight:700;padding:0 30px;text-shadow:0 1px 3px rgba(0,0,0,.6)}
.practice-card.featured{outline:12px solid var(--blue);align-items:flex-end;padding-bottom:20px;box-shadow:0 10px 30px rgba(0,0,0,.15)}

/* about */
.about-frame{left:527px;top:1414px;width:598px;height:240px;border:7px solid var(--blue);border-bottom:none}
.about-photo{left:600px;top:1463px;width:600px;height:512px;background:linear-gradient(135deg,#a7a9ab 0%,#6f7276 50%,#3e4145 100%)}
.about-box{left:0;top:1558px;width:600px;height:512px;background:var(--blue);color:var(--white);text-align:center;padding:72px 78px 0}
.about-box h2{font-size:31px}
.about-box .rule{background:var(--white)}
.about-box p{font-size:13.4px;line-height:25.7px;text-align:justify;text-align-last:center;margin-top:22px}
.btn-pill{display:inline-block;border-radius:20px;font-size:13px;font-weight:700;text-transform:uppercase}
.about-box .btn-pill{background:var(--white);color:var(--blue-dark);padding:11px 36px;margin-top:18px}

/* testimonials */
.testimonial{width:460px}
.quote-mark{font-family:'Roboto Slab',serif;font-size:64px;line-height:40px;color:var(--blue);height:40px;font-style:italic}
.testimonial p{font-size:13.4px;font-style:italic;color:var(--muted);line-height:25.5px;margin-top:10px;text-align:justify}
.author{display:flex;align-items:center;gap:14px;margin-top:14px}
.avatar{width:64px;height:64px;border-radius:50%}
.author-name{font-family:'Roboto Slab',serif;font-size:18px;color:var(--black)}
.author-co{font-size:13px;color:var(--ink);margin-top:4px}
.round-arrow{width:34px;height:34px;border-radius:50%;background:#e8e8e8;display:flex;align-items:center;justify-content:center}

/* contact */
.touch{top:2577px;left:0;width:1200px;height:666px;background:var(--black)}
.touch-blue{left:0;top:0;width:232px;height:666px;background:var(--blue)}
.touch h2{color:var(--white);top:105px}
.touch .rule{background:var(--white)}
.touch-photo{left:111px;top:183px;width:469px;height:381px;background:linear-gradient(160deg,#6b5b4c 0%,#9a8d7f 45%,#4a4f56 100%)}
.field{background:var(--white);border:1px solid #cfcfcf;font-size:12.5px;color:#555;padding:0 13px;display:flex;align-items:center}
.btn-send{background:var(--blue);color:var(--white);font-size:12.5px;font-weight:700;display:flex;align-items:center;justify-content:center;text-transform:uppercase}

/* industries */
.industries{top:3243px;left:0;width:1200px;height:405px;background:var(--light)}
.industries h2{left:111px;top:110px;font-size:31px;line-height:44px;color:var(--black);text-align:left}
.industries .rule{margin:14px 0 0}
.industries p{left:500px;top:107px;width:588px;font-size:13.4px;line-height:25.5px;color:var(--muted);text-align:justify}
.ind-btn{top:231px;width:307px;height:66px;background:var(--grey-btn);display:flex;align-items:center;justify-content:center;font-size:13px;font-weight:700;color:var(--black);text-transform:uppercase}
.ind-btn.active{background:var(--blue);color:var(--white)}

/* stories */
.story{top:3820px;width:308px;height:430px;background:var(--white);border:1px solid #e2e2e2;text-align:center}
.story.featured{box-shadow:0 8px 26px rgba(0,0,0,.14);border-color:transparent}
.story-img{width:100%;height:215px}
.story h3{font-size:21px;font-weight:500;color:var(--black);margin-top:26px}
.story p{font-size:13px;color:var(--muted);line-height:22px;padding:0 36px;margin-top:12px}
.story .btn-pill{margin-top:18px;padding:9px 38px;background:#dfe9f6;color:var(--blue-dark);font-size:12.5px;text-transform:none}
.story.featured .btn-pill{background:var(--blue-dark);color:var(--white)}

/* footer */
.site-footer{top:4336px;left:0;width:1200px;height:363px;background:var(--black);color:var(--white)}
.footer-col h4{font-size:19px;font-weight:500}
.footer-col .small{font-size:12px;line-height:21px;color:#ddd}
.foot-line{display:flex;align-items:center;gap:14px;font-size:12px;color:#ddd}
.foot-dot{width:26px;height:26px;border-radius:50%;background:var(--blue);flex:none;display:flex;align-items:center;justify-content:center}
.quick-links{list-style:none}
.quick-links li{font-size:12px;color:#ddd;height:21.5px;display:flex;align-items:center;gap:14px}
.quick-links li::before{content:"";width:9px;height:9px;border-radius:50%;background:var(--blue)}
.social{width:18px;height:18px;background:#ddd}
.copyright{left:0;top:330px;width:1200px;text-align:center;font-size:11.5px;color:#ddd}
</style>
</head>
<body>

<header class="site-header abs">
  <div class="brand abs">
    <div class="brand-mark"></div>
    <div class="brand-name">HAVERLOCK</div>
    <div class="brand-sub">TRIAL FIRM</div>
  </div>
  <div class="contact-item abs" style="left:615px">
    <div class="contact-icon"><svg width="16" height="16" viewBox="0 0 24 24"><path fill="#fff" d="M6.6 10.8a15 15 0 0 0 6.6 6.6l2.2-2.2c.3-.3.7-.4 1-.2 1.1.4 2.3.6 3.6.6.6 0 1 .4 1 1V20c0 .6-.4 1-1 1A17 17 0 0 1 3 4c0-.6.4-1 1-1h3.5c.6 0 1 .4 1 1 0 1.3.2 2.5.6 3.6.1.3 0 .7-.2 1z"/></svg></div>
    <div><div class="contact-label">Call us :</div><div class="contact-value">+1 888 888 8888</div></div>
  </div>
  <div class="contact-item abs" style="left:840px">
    <div class="contact-icon"><svg width="16" height="16" viewBox="0 0 24 24"><path fill="#fff" d="M3 5h18v14H3z"/><path d="M3 6l9 7 9-7" fill="none" stroke="#1565c8" stroke-width="2"/></svg></div>
    <div><div class="contact-label">Email Address :</div><div class="contact-value">info@companyname.com</div></div>
  </div>
  <nav class="main-nav abs">
    <ul>
      <li class="active">HOME</li><li>ABOUT US</li><li>PRACTICE AREAS</li><li>RESOURCES &amp; ADVISORIES</li><li>BLOG</li><li>CONTACT</li>
    </ul>
  </nav>
</header>

<section class="hero abs" role="img" aria-label="Business professionals shaking hands across a meeting table"></section>
<div class="hero-arrow abs" style="left:38px"><svg width="14" height="14" viewBox="0 0 14 14"><path d="M9 2L4 7l5 5" fill="none" stroke="#fff" stroke-width="2"/></svg></div>
<div class="hero-arrow abs" style="left:1120px"><svg width="14" height="14" viewBox="0 0 14 14"><path d="M5 2l5 5-5 5" fill="none" stroke="#fff" stroke-width="2"/></svg></div>
<div class="hero-banner abs">
  <div class="slant"></div>
  <div class="bracket l"></div><div class="bracket r"></div>
  <h1 class="display">Haverlock<br>Trial Firm PLLC</h1>
</div>

<h2 class="section-title display" style="top:838px">Our Practice Areas<div class="rule"></div></h2>
<div class="practice-card abs" style="left:111px;top:927px;background:linear-gradient(135deg,#5a5048,#2e2a26)" role="img" aria-label="Documents on a desk">Product Liability</div>
<div class="practice-card featured abs" style="left:449px;top:927px;background:linear-gradient(135deg,#4a5058,#23262b)" role="img" aria-label="Hands reviewing a contract">Premises Liability</div>
<div class="practice-card abs" style="left:784px;top:927px;background:linear-gradient(135deg,#7a7466,#3c3a34)" role="img" aria-label="Advisor meeting with an elderly couple">Professional Liability</div>
<div class="practice-card abs" style="left:111px;top:1149px;background:linear-gradient(135deg,#6a3034,#272224)" role="img" aria-label="Damaged car after a collision">Vehicle and Transportation Liability</div>
<div class="practice-card abs" style="left:449px;top:1149px;background:linear-gradient(135deg,#6a6660,#34322f)" role="img" aria-label="Signing a warranty form">Warranty Claims</div>
<div class="practice-card abs" style="left:784px;top:1149px;background:linear-gradient(135deg,#8a7a52,#3e3a30)" role="img" aria-label="Construction worker with tools">Construction Defects</div>

<div class="about-frame abs"></div>
<div class="about-photo abs" role="img" aria-label="Attorney reviewing a document with a client"></div>
<section class="about-box abs">
  <h2 class="display">About Us</h2><div class="rule"></div>
  <p>Lorem ipsum dolor sit amet, consectetur adipiscing elit, sed do eiusmod tempor incididunt ut labore et dolore magna aliqua. Ut enim ad minim veniam, quis nostrud exercitation ullamco laboris nisi ut aliquip ex ea commodo consequat. Duis aute irure dolor in reprehenderit in voluptate velit esse cillum dolore eu fugiat nulla pariatur. Excepteur sint occaecat cupidatat non proident, sunt in culpa qui officia deserunt mollit anim id est laborum. Lorem ipsum dolor sit amet, consectetur adipiscing elit, sed do eiusmod tempor incididunt ut labore et dolore magna aliqua.</p>
  <span class="btn-pill">Learn More</span>
</section>

<h2 class="section-title display" style="top:2170px">Satisfied Clients<div class="rule"></div></h2>
<div class="round-arrow abs" style="left:36px;top:2356px"><svg width="12" height="12" viewBox="0 0 12 12"><path d="M8 2L4 6l4 4" fill="none" stroke="#333" stroke-width="1.6"/></svg></div>
<div class="round-arrow abs" style="left:1128px;top:2356px"><svg width="12" height="12" viewBox="0 0 12 12"><path d="M4 2l4 4-4 4" fill="none" stroke="#333" stroke-width="1.6"/></svg></div>
<div class="testimonial abs" style="left:111px;top:2266px">
  <div class="quote-mark">&ldquo;</div>
  <p>Lorem ipsum dolor sit amet, consectetur adipiscing elit, sed do eiusmod tempor incididunt ut labore et dolore magna aliqua. Ut enim ad minim veniam, quis nostrud exercitation ullamco laboris nisi ut aliquip ex ea commodo consequat.</p>
  <div class="author"><div class="avatar" style="background:linear-gradient(135deg,#6b4a36,#2e241e)" role="img" aria-label="Portrait of Andre"></div><div><div class="author-name">- Andre</div><div class="author-co">Company name</div></div></div>
</div>
<div class="testimonial abs" style="left:633px;top:2266px">
  <div class="quote-mark">&ldquo;</div>
  <p>Lorem ipsum dolor sit amet, consectetur adipiscing elit, sed do eiusmod tempor incididunt ut labore et dolore magna aliqua. Ut enim ad minim veniam, quis nostrud exercitation ullamco laboris nisi ut aliquip ex ea commodo consequat.</p>
  <div class="author"><div class="avatar" style="background:linear-gradient(135deg,#c07a52,#7a3e2a)" role="img" aria-label="Portrait of Asha"></div><div><div class="author-name">- Asha</div><div class="author-co">Company name</div></div></div>
</div>

<section class="touch abs">
  <div class="touch-blue abs"></div>
  <h2 class="section-title display">Get In Touch<div class="rule"></div></h2>
  <div class="touch-photo abs" role="img" aria-label="Lawyers meeting around a table"></div>
  <div class="field abs" style="left:600px;top:183px;width:234px;height:44px">First name</div>
  <div class="field abs" style="left:854px;top:183px;width:235px;height:44px">Last name</div>
  <div class="field abs" style="left:600px;top:246px;width:234px;height:44px">Email</div>
  <div class="field abs" style="left:854px;top:246px;width:235px;height:44px">Phone</div>
  <div class="field abs" style="left:600px;top:309px;width:489px;height:44px;justify-content:space-between">Case type<svg width="10" height="6" viewBox="0 0 10 6"><path d="M1 1l4 4 4-4" fill="none" stroke="#777" stroke-width="1.3"/></svg></div>
  <div class="field abs" style="left:600px;top:372px;width:489px;height:127px;align-items:flex-start;padding-top:14px">Message</div>
  <div class="btn-send abs" style="left:600px;top:520px;width:234px;height:44px">Send Information</div>
</section>

<section class="industries abs">
  <h2 class="display abs">Industries<br>We Served<div class="rule"></div></h2>
  <p class="abs">Lorem ipsum dolor sit amet, consectetur adipiscing elit, sed do eiusmod tempor incididunt ut labore et dolore magna aliqua. Ut enim ad minim veniam, quis nostrud exercitation ullamco laboris nisi ut aliquip ex ea commodo consequat. Duis aute irure dolor in reprehenderit in voluptate velit esse cillum</p>
  <div class="ind-btn abs" style="left:111px">Lorem ipsum dolor sit</div>
  <div class="ind-btn active abs" style="left:447px">Lorem ipsum dolor sit</div>
  <div class="ind-btn abs" style="left:781px">Lorem ipsum dolor sit</div>
</section>

<h2 class="section-title display" style="top:3728px">Success Stories<div class="rule"></div></h2>
<div class="round-arrow abs" style="left:36px;top:4039px"><svg width="12" height="12" viewBox="0 0 12 12"><path d="M8 2L4 6l4 4" fill="none" stroke="#333" stroke-width="1.6"/></svg></div>
<div class="round-arrow abs" style="left:1128px;top:4039px"><svg width="12" height="12" viewBox="0 0 12 12"><path d="M4 2l4 4-4 4" fill="none" stroke="#333" stroke-width="1.6"/></svg></div>
<article class="story abs" style="left:111px">
  <div class="story-img" style="background:linear-gradient(135deg,#2b4a7a,#141c2a)" role="img" aria-label="Hand stacking coins beside a growth chart"></div>
  <h3>Lorem ipsum dolor sit</h3>
  <p>Lorem ipsum dolor sit amet, conse ctetur adipiscing elit, sed do eiusmod tempor incididunt ut</p>
  <span class="btn-pill">Read More</span>
</article>
<article class="story featured abs" style="left:446px">
  <div class="story-img" style="background:linear-gradient(135deg,#2f5a8a,#c9c3b8)" role="img" aria-label="Person reviewing bills with a calculator"></div>
  <h3>Lorem ipsum dolor sit</h3>
  <p>Lorem ipsum dolor sit amet, conse ctetur adipiscing elit, sed do eiusmod tempor incididunt ut</p>
  <span class="btn-pill">Read More</span>
</article>
<article class="story abs" style="left:781px">
  <div class="story-img" style="background:linear-gradient(135deg,#cfc7b8,#6a5a4c)" role="img" aria-label="Stressed businesswoman at a laptop"></div>
  <h3>Lorem ipsum dolor sit</h3>
  <p>Lorem ipsum dolor sit amet, conse ctetur adipiscing elit, sed do eiusmod tempor incididunt ut</p>
  <span class="btn-pill">Read More</span>
</article>

<footer class="site-footer abs">
  <div class="footer-col abs" style="left:111px;top:80px;width:230px">
    <h4>About us</h4>
    <p class="small" style="margin-top:26px">Lorem ipsum dolor sit amet, conse ctetur adipiscing elit, sed do eiu smod tempor incididunt ut labo re et dolore magna aliqua.</p>
    <div style="display:flex;gap:20px;margin-top:14px">
      <div class="social" aria-label="Social profile"></div><div class="social" aria-label="Social profile"></div><div class="social" aria-label="Social profile"></div>
    </div>
  </div>
  <div class="footer-col abs" style="left:376px;top:80px;width:220px">
    <h4>Contact us</h4>
    <div class="foot-line" style="margin-top:26px"><span class="foot-dot"><svg width="12" height="12" viewBox="0 0 24 24"><path fill="#fff" d="M12 2a7 7 0 0 0-7 7c0 5 7 13 7 13s7-8 7-13a7 7 0 0 0-7-7zm0 9.5A2.5 2.5 0 1 1 12 6.5a2.5 2.5 0 0 1 0 5z"/></svg></span><span>Lorem ipsum dolor sit<br>amet, cons</span></div>
    <div class="foot-line" style="margin-top:18px"><span class="foot-dot"><svg width="12" height="12" viewBox="0 0 24 24"><path fill="#fff" d="M6.6 10.8a15 15 0 0 0 6.6 6.6l2.2-2.2c.3-.3.7-.4 1-.2 1.1.4 2.3.6 3.6.6.6 0 1 .4 1 1V20c0 .6-.4 1-1 1A17 17 0 0 1 3 4c0-.6.4-1 1-1h3.5c.6 0 1 .4 1 1 0 1.3.2 2.5.6 3.6.1.3 0 .7-.2 1z"/></svg></span>+1 888 888 8888</div>
    <div class="foot-line" style="margin-top:18px"><span class="foot-dot"><svg width="12" height="12" viewBox="0 0 24 24"><path fill="#fff" d="M3 5h18v14H3z"/><path d="M3 6l9 7 9-7" fill="none" stroke="#1565c8" stroke-width="2"/></svg></span>info@companyname.com</div>
  </div>
  <div class="footer-col abs" style="left:625px;top:80px;width:180px">
    <h4>Quick Links</h4>
    <ul class="quick-links" style="margin-top:22px">
      <li>Home</li><li>About us</li><li>Practice Areas</li><li>Resources &amp; Advisories</li><li>Blog</li><li>Contact</li>
    </ul>
  </div>
  <div class="footer-col abs" style="left:823px;top:80px;width:270px">
    <h4>Subscribe Our Newsletter</h4>
    <div class="field" style="margin-top:28px;width:266px;height:38px;background:#1d1d1d;border-color:#2a2a2a;color:#ddd">Email address</div>
    <div class="btn-send" style="margin-top:12px;width:108px;height:36px;font-size:11.5px">Subscribe</div>
  </div>
  <div class="copyright abs">All Right Reserved © 2025 Haverlock Trial Firm PLLC</div>
</footer>

</body>
</html>
```